Health Spectrum and Energy Slides

Create beautiful and facinating PowerPoint slides that inspire and motivate

Target Market(s)

Clients looking for strategic breakthroughs and transformation

Industry/Entity Type

Health

Requirements
Must have
• Beautiful, heartfelt and fascinating graphics.
Nice to have
• Award winning designs.

```html
<!DOCTYPE html>
<html lang="en">
<head>
<meta charset="utf-8">
<title>Health Spectrum and Energy Slides</title>
<link rel="stylesheet" href="https://fonts.googleapis.com/css2?family=Open+Sans:ital,wght@0,400;0,600;0,700;1,400&display=swap">
<style>
:root{
  --page:#f2f2f2;
  --frame:#d2d2d2;
  --num:#7d7d7d;
  --white:#ffffff;
  --ink:#1d1d1d;
  --green:#3fbf3f;
  --red:#e0301e;
}
*{box-sizing:border-box;margin:0;padding:0}
html,body{width:1200px;height:824px;overflow:hidden;background:var(--page);font-family:"Open Sans",Arial,sans-serif}
.board{position:relative;width:1200px;height:824px}
.slide{position:absolute;width:371px;height:217px;overflow:hidden;outline:1px solid var(--frame);outline-offset:1px;color:var(--white)}
.slide-num{position:absolute;font-size:16px;color:var(--num)}
.fill{position:absolute;inset:0}
.abs{position:absolute}
.c1{left:16px}.c2{left:418px}.c3{left:820px}
.r1{top:28px}.r2{top:298px}.r3{top:567px}
.shadow{text-shadow:0 1px 2px rgba(0,0,0,.7)}

/* slide 2 */
.spec-title{font-size:5.6px;font-weight:700;line-height:1.25;color:var(--ink);text-align:center;width:62px}
.spec-title.right{color:var(--white)}
.spec-label{font-size:3.6px;line-height:1.2;width:50px}
.spec-label.left{text-align:right;color:var(--ink)}
.spec-label.water{color:#cfe6ff}

/* slide 3 */
.course-title{top:12px;width:100%;text-align:center;font-size:11.5px;font-weight:700}
.course-caption{bottom:18px;width:100%;text-align:center;font-size:6.8px;line-height:1.55}

/* slide 4 */
.mirror-rule{left:156px;top:74px;width:1px;height:72px;background:#bbb}
.mirror-text{left:162px;top:75px;width:152px;font-size:7.2px;line-height:1.35;color:#e6e6e6}
.mirror-text p+p{margin-top:8px}

/* slide 5 */
.portal-list{left:10px;top:11px;width:222px;font-size:4.9px;line-height:1.32;color:#e8e8e8}
.portal-list p{margin-bottom:5.2px}
.portal-list b{font-weight:700;color:var(--white)}
.brand{left:10px;bottom:11px;font-size:7px;color:#e8e8e8;display:flex;align-items:center;gap:4px}
.brand i{display:block;width:7px;height:7px;border-radius:50%;background:#e8e8e8}

/* slide 6 */
.charge-title{top:10px;width:100%;text-align:center;font-size:17.5px;font-weight:700}
.charge-sub{top:33px;width:100%;text-align:center;font-size:9px}
.list-head{font-size:5.5px;font-weight:700}
.energy-list{font-size:3.8px;line-height:1.32;text-align:center;width:62px}
.charge-foot{bottom:24px;width:100%;text-align:center;font-size:3.9px;line-height:1.3}

/* slide 7 */
.sky-title{top:70px;width:100%;text-align:center;font-family:Arial,"Open Sans",sans-serif;font-size:13.5px}
.sky-text{top:103px;width:100%;text-align:center;font-family:Arial,"Open Sans",sans-serif;font-size:13.5px;line-height:1.4}

/* slide 8 */
.drift{font-size:7.5px;font-style:italic;font-family:Georgia,serif;color:rgba(255,255,255,.92)}

/* slide 9 */
.menu-title{top:6px;width:100%;text-align:center;font-size:10.5px;font-weight:700;line-height:1.3}
.plate{position:absolute;width:90px;height:22px;border-radius:50%;background:radial-gradient(ellipse at 50% 35%,#ffffff 52%,#e2e2e2 70%,#b8b8b8 100%);box-shadow:0 2px 3px rgba(0,0,0,.4);font-size:4.8px;line-height:1.15;color:var(--ink);text-align:center;display:flex;align-items:flex-start;justify-content:center;padding-top:2px}
</style>
</head>
<body>
<main class="board">

  <!-- 1 -->
  <section class="slide c1 r1">
    <div class="fill" role="img" aria-label="Monochrome profile portrait of a man beside a towering maze on a black background"
      style="background:
        radial-gradient(ellipse 22% 40% at 92% 22%,rgba(200,200,200,.55),transparent 70%),
        radial-gradient(ellipse 18% 30% at 80% 62%,rgba(170,170,170,.45),transparent 70%),
        radial-gradient(ellipse 30% 55% at 70% 40%,rgba(120,120,120,.55),transparent 75%),
        linear-gradient(90deg,#040404 0%,#0b0b0b 45%,#2a2a2a 70%,#4a4a4a 85%,#1a1a1a 100%)"></div>
  </section>
  <span class="slide-num" style="left:18px;top:251px">1</span>

  <!-- 2 -->
  <section class="slide c2 r1">
    <div class="fill" role="img" aria-label="Half sunny, half stormy landscape with a lone tree on a grassy island above deep water"
      style="background:
        radial-gradient(ellipse 25% 30% at 5% 55%,rgba(255,230,60,.95),transparent 70%),
        radial-gradient(ellipse 14% 30% at 50% 35%,rgba(90,140,50,.85),transparent 70%),
        radial-gradient(ellipse 28% 10% at 48% 62%,rgba(80,130,40,.9),transparent 75%),
        radial-gradient(ellipse 30% 40% at 80% 20%,rgba(120,125,130,.6),transparent 70%),
        linear-gradient(90deg,#f2c83a 0%,#f3dc8a 22%,#b9c6cf 42%,#6b7278 62%,#3a3d42 80%,#2a2c30 100%)"></div>
    <div class="abs" role="img" aria-label="Underwater view beneath the island" style="left:0;top:146px;width:371px;height:71px;background:radial-gradient(ellipse 30% 60% at 48% 20%,rgba(90,150,110,.7),transparent 70%),linear-gradient(180deg,#2a83c8,#114a86 55%,#0a2646)"></div>
    <div class="abs" style="left:0;top:145px;width:371px;height:1.5px;background:#e8eef2"></div>
    <svg class="abs" style="left:0;top:0" width="371" height="217" viewBox="0 0 371 217">
      <path d="M100 56 C124 54,130 74,150 100 S190 118,225 126 S248 142,256 160 S262 190,270 190" fill="none" stroke="#fff" stroke-width="0.9"/>
      <line x1="100" y1="58" x2="100" y2="195" stroke="#fff" stroke-width=".5"/>
      <line x1="264" y1="58" x2="264" y2="190" stroke="#fff" stroke-width=".5"/>
    </svg>
    <div class="abs spec-title" style="left:5px;top:11px">OPTIMAL HEALTH TO DEATH MALADAPTIVE DIS-STRESS REACTION SPECTRUM</div>
    <div class="abs spec-title right" style="left:302px;top:8px">TRANSFORMATION TO DEATH ADAPTIVE RESPONSE SPECTRUM</div>
    <div class="abs spec-label left" style="left:48px;top:58px">Optimal Health Emotional, Biological, Structural &amp; Spiritual</div>
    <div class="abs spec-label left" style="left:48px;top:84px">Subconscious Stress</div>
    <div class="abs spec-label left" style="left:48px;top:103px">Subtle Dis-Stress &amp; Dis-Ease Ache</div>
    <div class="abs spec-label left water" style="left:48px;top:154px">Chronic Dis-Stress &amp; Dis-Ease Severe Pain</div>
    <div class="abs spec-label left water" style="left:48px;top:180px">Death Physical Emotional, Biological, Structural</div>
    <div class="abs spec-label" style="left:267px;top:58px">Transformation Conscious Heartful Intentional Choice &amp; Action</div>
    <div class="abs spec-label" style="left:267px;top:96px">Change: Correction Choice &amp; Action</div>
    <div class="abs spec-label" style="left:267px;top:119px">Conscious Awareness</div>
    <div class="abs spec-label" style="left:267px;top:135px">Therapy</div>
    <div class="abs spec-label water" style="left:267px;top:152px">Trauma: Subconscious Automatic Reaction</div>
    <div class="abs spec-label water" style="left:267px;top:180px">Death Physical Emotional, Biological, Structural</div>
  </section>
  <span class="slide-num" style="left:420px;top:251px">2</span>

  <!-- 3 -->
  <section class="slide c3 r1">
    <div class="fill" role="img" aria-label="Sailboat heeling on rough sea under dramatic storm clouds with sunlight breaking through"
      style="background:
        radial-gradient(ellipse 22% 25% at 52% 40%,rgba(235,225,190,.85),transparent 70%),
        radial-gradient(ellipse 12% 10% at 92% 55%,rgba(240,140,40,.85),transparent 70%),
        radial-gradient(ellipse 10% 12% at 10% 50%,rgba(230,150,60,.55),transparent 70%),
        radial-gradient(ellipse 40% 15% at 50% 85%,rgba(150,160,165,.5),transparent 70%),
        linear-gradient(180deg,#1e2327 0%,#4d565c 25%,#8a8e88 45%,#2f3a40 62%,#4b565c 78%,#1a2126 100%)"></div>
    <div class="abs course-title shadow">COURSE CORRECTION</div>
    <div class="abs course-caption shadow">When the seas turn how do you stay on course?<br>Who do you become in the face of fear and uncertainty?</div>
  </section>
  <span class="slide-num" style="left:822px;top:251px">3</span>

  <!-- 4 -->
  <section class="slide c1 r2">
    <div class="fill" role="img" aria-label="Black and white photo of an older man looking into a bathroom mirror that reflects a younger man"
      style="background:
        radial-gradient(ellipse 14% 30% at 22% 45%,rgba(160,160,160,.6),transparent 70%),
        radial-gradient(ellipse 12% 18% at 68% 25%,rgba(150,150,150,.55),transparent 70%),
        linear-gradient(90deg,#2e2e2e 0%,#555 18%,#3a3a3a 32%,#6a6a6a 45%,#8a8a8a 60%,#4c4c4c 80%,#6a6a6a 92%,#2a2a2a 100%)"></div>
    <div class="abs" style="left:150px;top:8px;width:134px;height:200px;border:3px solid rgba(200,200,200,.35)"></div>
    <div class="abs mirror-rule"></div>
    <div class="abs mirror-text shadow">
      <p>We don't see the truth. We see what we believe.</p>
      <p>When you change your beliefs you change what you see, feel and hear so your reflection in the world changes.</p>
    </div>
  </section>
  <span class="slide-num" style="left:18px;top:521px">4</span>

  <!-- 5 -->
  <section class="slide c2 r2">
    <div class="fill" role="img" aria-label="Dim room with bright light pouring through an open doorway on the right"
      style="background:
        radial-gradient(ellipse 18% 60% at 88% 55%,rgba(255,255,255,.85),transparent 70%),
        radial-gradient(ellipse 30% 35% at 75% 90%,rgba(200,205,210,.45),transparent 75%),
        linear-gradient(90deg,#15181c 0%,#23272c 45%,#4a4f55 65%,#9aa0a6 78%,#f3f4f5 86%,#b3b7bb 92%,#5d6166 100%)"></div>
    <div class="abs portal-list">
      <p><b>Doorway:</b> Problems are portals that enhance your awareness and compassion so you can become your Best Highest Self.</p>
      <p><b>Oneness:</b> You are not alone. Send out your thoughts and feelings. You will find support in predictable and unpredictable places.</p>
      <p><b>Impermanent:</b> Everything is impermanent. This is a temporary.</p>
      <p><b>Defuse &amp; Observe:</b> Observe, name and express your dis-ease and dis-stress. You are not the problem. You are not the emotion.</p>
      <p><b>Discern:</b> Is that True? Quality questions create a quality experience. If you could create your life in any way wanted would you even create it with this challenge?</p>
      <p><b>Heartfelt Desire:</b> If you could choose anything what would your <u>heart choose</u>?</p>
      <p><b>Dream:</b> Go to the land of your Heartfelt Desire <b><i>"AS IF"</i></b> you are already there! Welcome to the land of ________.</p>
      <p><b>Gratitude:</b> When you get a "Gift", what do you say? "Thank you." Or, "Infinite Love &amp; Gratitude!" Let your love open The Door to this portal.</p>
    </div>
    <div class="abs brand"><i></i>Harborlight Center</div>
  </section>
  <span class="slide-num" style="left:420px;top:521px">5</span>

  <!-- 6 -->
  <section class="slide c3 r2">
    <div class="fill" role="img" aria-label="Wind turbines along a winding river through green marshland at sunset"
      style="background:
        radial-gradient(ellipse 25% 12% at 55% 52%,rgba(245,200,140,.85),transparent 70%),
        radial-gradient(ellipse 18% 40% at 50% 85%,rgba(80,150,210,.85),transparent 70%),
        radial-gradient(ellipse 20% 25% at 15% 15%,rgba(90,140,220,.6),transparent 70%),
        linear-gradient(180deg,#2e62b5 0%,#5b8fd6 30%,#b9c7d6 48%,#d7a46a 54%,#4f7f3a 62%,#3c6c28 80%,#2d4f1e 100%)"></div>
    <div class="abs charge-title shadow">CHARGE ME UP!</div>
    <div class="abs charge-sub shadow">ENERGY USE AND RETENTION</div>
    <div class="abs list-head shadow" style="left:31px;top:55px">ENERGIZE</div>
    <div class="abs energy-list shadow" style="left:17px;top:63px">Love &amp; Loved<br>Heartfelt Breathing<br>Gratitude<br>Authentic, Action, Awe<br>Caring, Cared For<br>Commitment, Let Go<br>I Don't Control Others<br>Guided Session<br>Meditation<br>Nature, Oneness<br>Success, Small Play<br>Progress, Patience<br>Positive + Surprise<br>Peace, Responsible<br>See Potential<br>See Opportunity<br>Student Mindset<br>Sleep, Not Alone<br>Values Centered Action</div>
    <div class="abs list-head shadow" style="left:310px;top:56px">EXHAUST</div>
    <div class="abs energy-list shadow" style="left:293px;top:64px">Anger, Anxiety<br>Blame, Compare<br>Need Control<br>Envy, Entitlement<br>Expect The Worst<br>Fear, Frustration<br>Greed, Lack<br>Negative-surprise<br>Mask, Want More<br>Procrastinate<br>Resentment, Shame<br>Victim, Why Me</div>
    <svg class="abs" style="left:0;top:0" width="371" height="217" viewBox="0 0 371 217">
      <path d="M103 140 V90 M98 97 L103 88 L108 97" fill="none" stroke="var(--green)" stroke-width="3"/>
      <path d="M269 88 V138 M264 131 L269 140 L274 131" fill="none" stroke="var(--red)" stroke-width="3"/>
      <g fill="none" stroke="#fff" stroke-width="3">
        <rect x="116" y="87" width="30" height="48" rx="2"/>
        <rect x="153" y="87" width="30" height="48" rx="2"/>
        <rect x="190" y="87" width="30" height="48" rx="2"/>
        <rect x="227" y="87" width="30" height="48" rx="2"/>
      </g>
      <g fill="#fff">
        <rect x="125" y="82" width="12" height="4"/><rect x="162" y="82" width="12" height="4"/><rect x="199" y="82" width="12" height="4"/><rect x="236" y="82" width="12" height="4"/>
        <rect x="121" y="93" width="20" height="5"/><rect x="121" y="102" width="20" height="5"/><rect x="121" y="111" width="20" height="5"/><rect x="121" y="120" width="20" height="5"/>
        <rect x="158" y="102" width="20" height="5"/><rect x="158" y="111" width="20" height="5"/><rect x="158" y="120" width="20" height="5"/>
        <rect x="195" y="111" width="20" height="5"/><rect x="195" y="120" width="20" height="5"/>
        <rect x="232" y="120" width="20" height="5"/>
      </g>
    </svg>
    <div class="abs charge-foot shadow">Awareness Aligned Balance Clear Conscious Capacity Creative<br>Co-create Choice Determined Disciplined Ease Flexible Focus Flow<br>Presence Resilient Recovery Rebound Replenish Renew Sleep<br>Strong Stable Willpower Leaks Weak Drain</div>
  </section>
  <span class="slide-num" style="left:822px;top:521px">6</span>

  <!-- 7 -->
  <section class="slide c1 r3">
    <div class="fill" role="img" aria-label="Starry night sky fading to a purple, pink and orange sunset over a dark horizon"
      style="background:
        radial-gradient(ellipse 35% 14% at 55% 86%,rgba(255,170,120,.7),transparent 70%),
        radial-gradient(ellipse 60% 30% at 30% 80%,rgba(150,70,140,.55),transparent 75%),
        radial-gradient(ellipse 40% 30% at 75% 15%,rgba(40,50,90,.6),transparent 70%),
        linear-gradient(180deg,#04060d 0%,#0b1024 40%,#2b2550 62%,#8b4a86 76%,#e0708a 86%,#f28a3a 94%,#2a1208 98%)"></div>
    <div class="abs sky-title">BE THE SKY</div>
    <div class="abs sky-text">The Sky has room for all types of<br>changing weather and all the seasons.</div>
  </section>
  <span class="slide-num" style="left:18px;top:790px">7</span>

  <!-- 8 -->
  <section class="slide c2 r3">
    <div class="fill" role="img" aria-label="Curly haired child blowing dandelion seeds into soft glowing bokeh light"
      style="background:
        radial-gradient(ellipse 22% 35% at 30% 40%,rgba(255,255,255,.75),transparent 70%),
        radial-gradient(ellipse 16% 22% at 60% 70%,rgba(255,255,255,.6),transparent 70%),
        radial-gradient(ellipse 22% 45% at 78% 62%,rgba(210,110,50,.85),transparent 70%),
        radial-gradient(ellipse 30% 20% at 45% 100%,rgba(110,160,60,.7),transparent 70%),
        linear-gradient(120deg,#d7dfd8 0%,#c3cdc6 35%,#e9d3a8 60%,#eea055 85%,#d9762a 100%)"></div>
    <span class="abs drift" style="left:218px;top:6px;transform:rotate(-5deg)">Hopeless</span>
    <span class="abs drift" style="left:136px;top:28px">Unlovable</span>
    <span class="abs drift" style="left:28px;top:52px;transform:rotate(-55deg)">Not Good Enough</span>
    <span class="abs drift" style="left:136px;top:88px;transform:rotate(55deg)">Why Me</span>
    <span class="abs drift" style="left:170px;top:100px">Sad</span>
    <span class="abs drift" style="left:206px;top:122px;transform:rotate(-35deg)">Anger</span>
    <span class="abs drift" style="left:96px;top:138px">Fear</span>
    <span class="abs drift" style="left:132px;top:146px;transform:rotate(35deg)">Anxiety</span>
    <span class="abs drift" style="left:24px;top:134px;transform:rotate(-60deg)">Give up</span>
    <span class="abs drift" style="left:8px;top:162px;transform:rotate(-60deg)">Fake</span>
    <span class="abs drift" style="left:40px;top:168px;transform:rotate(-30deg)">Failure</span>
    <span class="abs drift" style="left:118px;top:190px;transform:rotate(-15deg)">Hurt</span>
    <span class="abs drift" style="left:156px;top:192px;transform:rotate(-40deg)">Loss</span>
  </section>
  <span class="slide-num" style="left:420px;top:790px">8</span>

  <!-- 9 -->
  <section class="slide c3 r3">
    <div class="fill" role="img" aria-label="Blurred warm restaurant interior with glowing lights above a wooden table top"
      style="background:
        radial-gradient(ellipse 12% 18% at 20% 15%,rgba(255,220,150,.85),transparent 70%),
        radial-gradient(ellipse 10% 15% at 75% 12%,rgba(255,230,170,.8),transparent 70%),
        radial-gradient(ellipse 14% 20% at 55% 40%,rgba(240,170,100,.6),transparent 70%),
        linear-gradient(180deg,#e9c18e 0%,#b6784a 28%,#6e4833 52%,#a86f42 68%,#c48a55 80%,#7a4f2e 100%)"></div>
    <div class="abs menu-title shadow">YOUR RESTAURANT:<br>YOU CAN EAT ANYTHING THAT YOU WANT AT</div>
    <div class="plate" style="left:0;top:58px">Least<br>Favorite Food</div>
    <div class="plate" style="left:276px;top:58px">Favorite<br>Food</div>
    <div class="plate" style="left:2px;top:143px">Heartfelt<br>Desire</div>
    <div class="plate" style="left:92px;top:145px">Pleasurable<br>Emotions</div>
    <div class="plate" style="left:184px;top:143px">Neutral<br>Emotions</div>
    <div class="plate" style="left:274px;top:143px">Neutral<br>Food</div>
    <div class="plate" style="left:22px;top:168px">Uncomfortable<br>Emotions</div>
    <div class="plate" style="left:130px;top:170px">Painful<br>Emotions</div>
    <div class="plate" style="left:232px;top:168px">Favorite<br>Emotions</div>
  </section>
  <span class="slide-num" style="left:822px;top:790px">9</span>

</main>
</body>
</html>
```